Quillfern Vaults - Direct Mailer / Flyer

We are excited to announce the launch of our new company, Quillfern Vaults, a premier cohosting facility and data center dedicated to Cryptocurrency Miners. Our website, https://quillfernvaults.example, provides detailed information about our offerings and showcases the innovative design schemes for the entire project.

Quillfern Vaults stands out in the industry by offering both GPU Hosting and ASIC Hosting services in our state-of-the-art facility, equipped with an impressive 17 Megawatts of available power. What sets us apart is our unique billing system based on actual metered power usage. We charge $0.08 for ASIC miners and $0.09 for GPU miners, ensuring cost-effectiveness and transparency for our clients.

Our commitment to excellence is evident in our use of cutting-edge technology, top-notch facilities, and strategic partnerships. These elements come together to deliver exceptional solutions tailored for real-world applications in the cryptocurrency space.

As part of our promotional efforts, we are developing a direct mailer/flyer to introduce Quillfern Vaults to a wider audience. This promotional material will also serve as a handout at events, to potential customers, and more. We welcome creative ideas and suggestions to maximize the versatility of this design and reach diverse target audiences effectively.

For a comprehensive overview of our services and to explore our design concepts, please visit https://quillfernvaults.example. Quillfern Vaults is poised to revolutionize the mining industry, and we look forward to partnering with you for success in the digital currency era.

```html
<!DOCTYPE html>
<html lang="en">
<head>
<meta charset="utf-8">
<title>Quillfern Vaults – Cohosting Flyer</title>
<link href="https://fonts.googleapis.com/css2?family=Poppins:wght@400;500;600;700&display=swap" rel="stylesheet">
<style>
:root{
  --ink:#141414;
  --blue:#2f55f5;
  --blue-deep:#2a47d8;
  --blue-soft:#3a5ff2;
  --sky:#dce7f7;
  --sky-light:#f1f6fd;
  --stage:#8f8f8f;
  --line:#9aa3b4;
}
*{margin:0;padding:0;box-sizing:border-box}
html,body{width:1200px;height:2287px;overflow:hidden}
body{background:var(--stage);font-family:'Poppins',sans-serif;color:var(--ink);position:relative}
.flyer{position:absolute;left:27px;top:403px;width:1022px;height:1322px;background:#fff;
  transform:scale(1.12);transform-origin:top left;overflow:hidden;box-shadow:0 14px 40px rgba(0,0,0,.35)}
.abs{position:absolute;z-index:3}

/* header */
.header{left:0;top:0;width:1022px;height:373px;background:linear-gradient(180deg,var(--sky-light) 0%,var(--sky) 100%);z-index:0}
.brand{left:53px;top:55px;display:flex;align-items:center;gap:14px}
.brand-mark{width:46px;height:44px;background:var(--ink);border-radius:3px}
.brand-name{font-weight:700;font-size:40px;letter-spacing:1px;text-transform:uppercase;color:var(--ink);line-height:1}
.headline{left:53px;top:145px;font-weight:700;font-size:52px;line-height:55px;letter-spacing:-.5px}
.headline .accent{color:var(--blue)}
.dots{left:53px;top:269px;display:flex;gap:4px}
.dots span{width:8px;height:8px;background:#8a8f9a}
.subline{left:53px;top:290px;font-weight:500;font-size:21px;line-height:27px;width:510px}
.hero-art{left:575px;top:30px;width:447px;height:345px;z-index:1;
  background:radial-gradient(ellipse at 60% 35%,#f1c592 0%,rgba(241,197,146,0) 40%),
  linear-gradient(180deg,rgba(200,212,232,0) 0%,#b8c4d8 70%,#2b2f38 92%,rgba(43,47,56,0) 100%)}

/* services band */
.services{left:0;top:373px;width:1022px;height:204px;display:flex}
.service{flex:1;color:#fff;text-align:center;padding:30px 26px 0;background:var(--blue-soft)}
.service:nth-child(odd){background:var(--blue-deep)}
.service svg{width:48px;height:48px;display:block;margin:0 auto 8px}
.service h3{font-weight:600;font-size:19px;line-height:24px;margin-bottom:6px}
.service p{font-size:13.5px;line-height:16px;opacity:.95}

/* commitment */
.commit-title{left:55px;top:606px;font-size:19px;font-weight:400;letter-spacing:-.2px}
.commit-title b{color:var(--blue);font-weight:600}
.pillars{left:40px;top:650px;display:flex}
.pillar{width:137px;text-align:center;font-size:14.5px;line-height:17px;border-right:1px dashed var(--line);padding-bottom:6px}
.pillar:last-child{border-right:none}
.pillar-icon{width:54px;height:54px;margin:0 auto 14px;border:3px solid var(--blue);border-radius:6px;background:#2b2e35;display:flex;align-items:center;justify-content:center}
.pillar-icon svg{width:32px;height:32px}
.pillar-note{left:461px;top:652px;width:172px;font-size:14.5px;line-height:17px}
.divider{left:53px;top:773px;width:570px;border-top:1px dashed var(--line)}
.intro{left:53px;top:797px;width:560px;font-size:14.5px;line-height:17.5px}
.intro b{color:var(--blue);font-weight:600}
.prices{left:54px;top:878px;display:flex;gap:12px}
.price{display:flex;height:43px;border-radius:5px;overflow:hidden}
.price-value{background:#2b2d33;color:#fff;font-weight:700;font-size:27px;width:110px;display:flex;align-items:center;justify-content:center;border:2px solid #2b2d33}
.price-value sup{font-size:13px;margin-right:1px;position:relative;top:-4px}
.price-label{background:var(--blue);color:#fff;font-size:15px;line-height:16px;width:95px;padding:5px 0 0 16px}
.note{left:55px;top:936px;font-size:13.5px}
.device-art{left:650px;top:615px;width:360px;height:360px;border-radius:40%;z-index:1;
  background:radial-gradient(ellipse at 55% 45%,#3a3c44 0%,#5b5f6a 28%,#eec39a 48%,rgba(240,205,170,.5) 62%,rgba(255,255,255,0) 72%)}

/* bottom */
.man-art{left:0;top:970px;width:420px;height:352px;z-index:1;
  background:linear-gradient(180deg,rgba(225,233,246,0) 0%,#c9d4e8 45%,#b08a5a 82%,#9aa0a8 100%)}
.chart{left:0;top:1030px;z-index:0}
.features{left:435px;top:995px;display:flex}
.feature{width:120px;text-align:center;font-weight:500;font-size:15.5px;line-height:18px;border-right:1px dashed var(--line)}
.feature:last-child{border-right:none;width:150px}
.feature svg{width:36px;height:36px;display:block;margin:0 auto 8px}
.closing{left:439px;top:1103px;width:560px;font-size:16px;line-height:19px}
.closing b{color:var(--blue);font-weight:600}
.contacts{left:441px;top:1183px;display:flex;gap:34px;font-size:20px;font-weight:500;align-items:center}
.contacts span{display:flex;align-items:center;gap:10px}
.contacts svg{width:24px;height:24px}
.url-bar{left:440px;top:1230px;width:582px;height:92px;background:var(--blue);border-radius:60px 0 0 0;z-index:2}
.url{left:440px;top:1258px;width:582px;text-align:center;color:#fff;font-size:26px;letter-spacing:3px;font-weight:400}
.url b{font-weight:700}
</style>
</head>
<body>
<main class="flyer">
  <section class="abs header"></section>
  <div class="abs hero-art" role="img" aria-label="Team working at a table on a giant tablet with golden crypto coins falling above and grey bar chart behind"></div>

  <div class="abs brand"><span class="brand-mark"></span><span class="brand-name">Quillfern Vaults</span></div>
  <h1 class="abs headline">Transform Mining<br><span class="accent">With Cohosting</span></h1>
  <div class="abs dots"><span></span><span></span><span></span><span></span><span></span><span></span></div>
  <p class="abs subline">Miners deserve the best - choose the hosting company that delivers excellence!</p>

  <section class="abs services">
    <div class="service">
      <svg viewBox="0 0 48 48" fill="none" stroke="#fff" stroke-width="2"><rect x="10" y="10" width="28" height="28" rx="3"/><rect x="15" y="15" width="18" height="18"/><text x="24" y="27.5" font-size="8" fill="#fff" stroke="none" text-anchor="middle" font-family="Poppins,sans-serif">GPU</text><path d="M16 4v6M22 4v6M28 4v6M34 4v6M16 38v6M22 38v6M28 38v6M34 38v6M4 16h6M4 24h6M4 32h6M38 16h6M38 24h6M38 32h6"/></svg>
      <h3>GPU Hosting</h3>
      <p>Begin your GPU Hosting journey with rates starting at $0.09 kWh, accepting all equipment.</p>
    </div>
    <div class="service">
      <svg viewBox="0 0 48 48" fill="none" stroke="#fff" stroke-width="2"><rect x="6" y="10" width="36" height="32" rx="3"/><circle cx="24" cy="26" r="10"/><path d="M17 19l14 14M31 19L17 33M16 6h16v4"/></svg>
      <h3>ASIC Hosting</h3>
      <p>Get your ASICs directly from us or send yours in today, starting at an all-in rate of $0.08 kWh.</p>
    </div>
    <div class="service">
      <svg viewBox="0 0 48 48" fill="none" stroke="#fff" stroke-width="2"><rect x="10" y="4" width="14" height="40" rx="2"/><path d="M13 12h8M13 18h8M13 24h8"/><circle cx="35" cy="26" r="7"/><text x="35" y="29" font-size="9" fill="#fff" stroke="none" text-anchor="middle" font-family="Poppins,sans-serif">₿</text></svg>
      <h3>Mining Hardware</h3>
      <p>Looking for mining hardware? Our equipment comes with no additional markup, ever.</p>
    </div>
    <div class="service">
      <svg viewBox="0 0 48 48" fill="none" stroke="#fff" stroke-width="2"><circle cx="20" cy="20" r="12"/><circle cx="30" cy="30" r="12"/><path d="M24 36h12M24 30h12"/></svg>
      <h3>Crypto Consulting</h3>
      <p>Enjoy complete White Glove Services for setup, insurance, and tax consulting.</p>
    </div>
  </section>

  <h2 class="abs commit-title">OUR COMMITMENT TO <b>EXCELLENCE IS EVIDENT IN OUR USE OF</b></h2>
  <div class="abs pillars">
    <div class="pillar"><div class="pillar-icon"><svg viewBox="0 0 32 32" fill="none" stroke="#fff" stroke-width="2"><circle cx="16" cy="16" r="11"/><circle cx="16" cy="16" r="5"/></svg></div>Cutting-edge<br>technology</div>
    <div class="pillar"><div class="pillar-icon"><svg viewBox="0 0 32 32" fill="none" stroke="#fff" stroke-width="2"><path d="M16 5l11 6-11 6-11-6z"/><path d="M5 16l11 6 11-6M5 21l11 6 11-6"/></svg></div>Top-notch<br>facilities</div>
    <div class="pillar"><div class="pillar-icon"><svg viewBox="0 0 32 32" fill="none" stroke="#fff" stroke-width="2"><path d="M4 14l7-6 5 3 5-3 7 6-10 10z"/><path d="M12 16l4 4 4-4"/></svg></div>Strategic<br>partnerships</div>
  </div>
  <p class="abs pillar-note">These elements come together to deliver exceptional solutions tailored for real-world applications in the cryptocurrency space.</p>
  <div class="abs divider"></div>
  <p class="abs intro">Quillfern Vaults stands out in the industry by offering both <b>GPU Hosting and ASIC Hosting</b> services in our state-of-the-art facility, equipped with an impressive 17 Megawatts of available power.What sets us apart is our unique billing system based on actual metered power usage.</p>
  <div class="abs prices">
    <div class="price"><div class="price-value"><sup>$</sup>0.08</div><div class="price-label">For ASIC<br>miners</div></div>
    <div class="price"><div class="price-value"><sup>$</sup>0.09</div><div class="price-label">For GPU<br>miners</div></div>
  </div>
  <p class="abs note">ensuring cost-effectiveness and transparency for our clients.</p>
  <div class="abs device-art" role="img" aria-label="Smartphone showing a crypto trading chart surrounded by stacks of gold coins"></div>

  <svg class="abs chart" width="440" height="292" viewBox="0 0 440 292" aria-hidden="true">
    <g fill="#dfe6f6"><rect x="20" y="160" width="22" height="132"/><rect x="60" y="120" width="22" height="172"/><rect x="100" y="180" width="22" height="112"/><rect x="140" y="90" width="22" height="202"/><rect x="340" y="70" width="22" height="222"/><rect x="380" y="130" width="22" height="162"/></g>
    <polyline points="0,180 60,130 120,150 200,80 280,110 360,40 430,60" fill="none" stroke="#c7d3ee" stroke-width="2"/>
  </svg>
  <div class="abs man-art" role="img" aria-label="Miner in a hard hat leaning over a pile of gold coins on a silver rock"></div>

  <div class="abs features">
    <div class="feature"><svg viewBox="0 0 36 36" fill="none" stroke="#2f55f5" stroke-width="2"><path d="M18 3l12 5v9c0 8-6 13-12 16-6-3-12-8-12-16V8z"/><path d="M12 18l4 4 8-8"/></svg>New Secure<br>Facility</div>
    <div class="feature"><svg viewBox="0 0 36 36" fill="none" stroke="#2f55f5" stroke-width="2"><circle cx="20" cy="20" r="12"/><path d="M20 13v7l5 3M17 4h6M2 16h6M4 22h5"/></svg>Speedy<br>Support</div>
    <div class="feature"><svg viewBox="0 0 36 36" fill="none" stroke="#2f55f5" stroke-width="2"><rect x="3" y="6" width="24" height="18" rx="2"/><path d="M10 30h10M15 24v6"/><circle cx="27" cy="22" r="6" fill="#fff"/><path d="M27 19v3l2 2"/></svg>99.45%<br>Uptime</div>
    <div class="feature"><svg viewBox="0 0 36 36" fill="none" stroke="#2f55f5" stroke-width="2"><circle cx="18" cy="16" r="11"/><text x="18" y="19" font-size="8" fill="#2f55f5" stroke="none" text-anchor="middle" font-family="Poppins,sans-serif">24/7</text><path d="M8 24l-2 8 8-3"/></svg>24/7 Remote<br>Access</div>
  </div>
  <p class="abs closing">Quillfern Vaults is poised to <b>revolutionize the mining industry</b>, and we look forward to partnering with you for <b>success in the digital currency era</b></p>
  <div class="abs contacts">
    <span><svg viewBox="0 0 24 24"><circle cx="12" cy="12" r="11" fill="#2f55f5"/><path d="M8 6l2 3-1 2c1 2 2 3 4 4l2-1 3 2-1 2c-5 0-10-5-10-10z" fill="#fff"/></svg>555 0142 7788</span>
    <span><svg viewBox="0 0 24 24" fill="none" stroke="#2f55f5" stroke-width="2"><rect x="2" y="5" width="20" height="14"/><path d="M2 5l10 8 10-8"/></svg>hello@quillfernvaults.example</span>
  </div>
  <div class="abs url-bar"></div>
  <p class="abs url">www.<b>quillfernvaults</b>.example</p>
</main>
</body>
</html>
```